Vacation Rental Postcard Design

The Kingfisher's Perch is a vacation rental cottage. We want a postcard that can be used as promotional give-aways for visitors as well as something that can be given to the tourism board and local merchants to help us promote the rental.

Our tag line is" The Kingfisher's Perch - the finest perch on the ridge!". Should also include "Snohomish, WA USA"

We have also used "Come see what all of the buzz is about"

Want to include our info in small print on the mailing side portion of the postcard:

KLWT: www.klwtstays.example/417294
Chatterly: www.chatterly.example/thefinestperchontheridge

Target Market(s)

Couples, romantic, honeymooners, coming for wine tasting, hot air ballooning, hiking, enjoying nature

Industry/Entity Type

Tourism

```html
<!DOCTYPE html>
<html lang="en">
<head>
<meta charset="utf-8">
<title>The Kingfisher's Perch – Postcard</title>
<link rel="stylesheet" href="https://fonts.googleapis.com/css2?family=Great+Vibes&family=Roboto+Condensed:ital,wght@0,400;0,700;1,700&display=swap">
<style>
  :root {
    --page: #efe9dd;
    --sage: #8f9f66;
    --frame: #e8dfc0;
    --band: #ddd3b0;
    --cream: #f4ead0;
    --ink: #1e1e1e;
    --white: #ffffff;
    --rule: #b9b9b9;
    --accent: #e0582a;
    --link-blue: #2f63b3;
  }
  * { box-sizing: border-box; margin: 0; padding: 0; }
  html, body { width: 1200px; height: 500px; overflow: hidden; }
  body { background: var(--page); font-family: "Roboto Condensed", sans-serif; position: relative; }

  .card { position: absolute; top: 42px; height: 433px; overflow: hidden; }
  .card--front { left: 25px; width: 560px; background: var(--sage); }
  .card--back { left: 612px; width: 558px; background: var(--white); }

  .photo { position: absolute; border: 4px solid var(--frame); }

  /* Front */
  .brand-mark { position: absolute; left: 22px; top: 40px; width: 120px; text-align: center; }
  .brand-mark__dot { display: block; width: 46px; height: 46px; border-radius: 50%; background: var(--ink); margin: 0 auto 8px; }
  .brand-mark__name { font-weight: 700; font-size: 14px; color: var(--ink); line-height: 1.1; }

  .hero-banner { position: absolute; left: 155px; top: 0; width: 405px; height: 84px;
    background: linear-gradient(90deg, #a8742e, #d99a3a 40%, #b9862f 70%, #8a6a2a); }
  .hero-banner__title { position: absolute; left: 14px; top: 6px; font-family: "Great Vibes", cursive;
    font-size: 40px; color: var(--white); text-shadow: 1px 1px 2px #3a2a10; white-space: nowrap; }
  .hero-banner__tag { position: absolute; left: 20px; top: 54px; font-weight: 700; font-size: 19px;
    color: var(--cream); text-shadow: 1px 1px 2px #3a2a10; white-space: nowrap; }
  .hero-banner__place { position: absolute; right: 14px; top: 60px; font-weight: 700; font-size: 13px;
    color: var(--cream); text-shadow: 1px 1px 2px #3a2a10; white-space: nowrap; }

  .photo--main { left: 155px; top: 96px; width: 380px; height: 212px;
    background: linear-gradient(180deg, #6d6f78 0%, #8d8a86 35%, #4b5a35 60%, #5f7a3a 100%); }
  .photo--main .caption { position: absolute; left: 10px; bottom: 10px; font-weight: 700; font-style: italic;
    font-size: 18px; color: var(--white); text-shadow: 1px 1px 2px #000; white-space: nowrap; }

  .photo--house { left: 17px; top: 150px; width: 126px; height: 158px;
    background: linear-gradient(180deg, #7fb2e0 0%, #3f6f45 55%, #a89a80 100%); }
  .photo--living { left: 17px; top: 318px; width: 126px; height: 97px;
    background: linear-gradient(180deg, #c8b27c, #8a5a30); }
  .photo--bedroom { left: 153px; top: 318px; width: 127px; height: 97px;
    background: linear-gradient(180deg, #d8c690, #eeeae0 60%, #6a8a50); }
  .photo--dining { left: 287px; top: 318px; width: 128px; height: 97px;
    background: linear-gradient(180deg, #c9b27a, #7a4a2a); }
  .photo--exterior { left: 421px; top: 318px; width: 117px; height: 97px;
    background: linear-gradient(180deg, #5a9ee0 0%, #2a2a2a 50%, #5a7a3a 100%); }

  /* Back */
  .message-side { position: absolute; left: 0; top: 0; width: 298px; height: 100%; background: var(--sage); }
  .message-side__title { position: absolute; left: 22px; top: 14px; font-family: "Great Vibes", cursive;
    font-size: 28px; color: var(--white); text-shadow: 1px 1px 1px #3a3a20; white-space: nowrap; }
  .message-side__tag { position: absolute; left: 30px; top: 54px; font-weight: 700; font-size: 15px; color: var(--cream); white-space: nowrap; }
  .message-side__place { position: absolute; left: 30px; top: 73px; font-weight: 700; font-size: 11px; color: var(--cream); white-space: nowrap; }
  .message-side__copy { position: absolute; width: 262px; font-weight: 700; font-size: 13px;
    line-height: 1.4; color: var(--white); white-space: nowrap; }
  .copy--intro { top: 90px; left: 34px; }
  .copy--rooms { top: 134px; left: 22px; }
  .photo--sunset { left: 43px; top: 182px; width: 207px; height: 158px; border: none;
    transform: rotate(2deg); box-shadow: 2px 3px 6px rgba(0,0,0,.35); z-index: 2;
    background: linear-gradient(180deg, #f07a9a 0%, #f5a070 45%, #7a3a40 75%, #1f1a1e 100%); }

  .contact-band { position: absolute; left: 0; top: 330px; width: 298px; height: 103px; background: var(--band); }
  .contact-band__badges { position: absolute; top: 22px; left: 0; width: 100%; display: flex; justify-content: center; gap: 18px; }
  .badge { display: flex; align-items: center; gap: 5px; font-weight: 700; font-size: 18px; color: var(--link-blue); }
  .badge__square { width: 18px; height: 18px; background: var(--link-blue); }
  .contact-band__links { position: absolute; top: 60px; width: 100%; text-align: center;
    font-weight: 700; font-size: 13px; line-height: 1.3; color: var(--accent); white-space: nowrap; }

  .brand-mark--back { left: 322px; top: 30px; width: 110px; }
  .stamp-box { position: absolute; left: 455px; top: 13px; width: 88px; height: 93px; border: 1px solid var(--rule); }
  .address-lines { position: absolute; left: 327px; top: 212px; width: 216px; }
  .address-lines span { display: block; height: 34px; border-top: 1px solid var(--rule); }
</style>
</head>
<body>
  <section class="card card--front">
    <div class="brand-mark">
      <span class="brand-mark__dot"></span>
      <span class="brand-mark__name">The Kingfisher's Perch</span>
    </div>
    <div class="hero-banner" role="img" aria-label="Autumn forest path with golden leaves">
      <div class="hero-banner__title">The Kingfisher's Perch</div>
      <div class="hero-banner__tag">The Finest On The Ridge</div>
      <div class="hero-banner__place">Snohomish, WA USA</div>
    </div>
    <div class="photo photo--main" role="img" aria-label="Grounds of the cottage under a stormy sky with a rainbow over tall evergreens">
      <p class="caption">Come see what all of the buzz is about</p>
    </div>
    <div class="photo photo--house" role="img" aria-label="Green two-storey cottage exterior with stone steps"></div>
    <div class="photo photo--living" role="img" aria-label="Living room with sofa and wood floors"></div>
    <div class="photo photo--bedroom" role="img" aria-label="Bedroom with white bedding"></div>
    <div class="photo photo--dining" role="img" aria-label="Dining area with flowers on the table"></div>
    <div class="photo photo--exterior" role="img" aria-label="Dark cottage exterior against blue sky"></div>
  </section>

  <section class="card card--back">
    <div class="message-side">
      <div class="message-side__title">The Kingfisher's Perch</div>
      <div class="message-side__tag">The Finest Perch On The Ridge</div>
      <div class="message-side__place">Snohomish, WA USA</div>
      <p class="message-side__copy copy--intro">Private view cottage on two country acres,<br>Romantic, refreshing, relaxing, reconnect.</p>
      <p class="message-side__copy copy--rooms">1 bedroom, 1.5 bath apartment, spectacular<br>mountain, valley and river view.</p>
      <div class="photo photo--sunset" role="img" aria-label="Pink sunset sky over silhouetted evergreen trees"></div>
      <div class="contact-band">
        <div class="contact-band__badges">
          <span class="badge"><span class="badge__square"></span>Chatterly</span>
          <span class="badge">KLWT</span>
        </div>
        <p class="contact-band__links">KLWT: www.klwtstays.example/417294<br>www.chatterly.example/thefinestperchontheridge</p>
      </div>
    </div>
    <div class="brand-mark brand-mark--back">
      <span class="brand-mark__dot"></span>
      <span class="brand-mark__name">The Kingfisher's Perch</span>
    </div>
    <div class="stamp-box"></div>
    <div class="address-lines"><span></span><span></span><span></span><span></span></div>
  </section>
</body>
</html>
```